Modern Business Card for Larkwell 2018

Our company assumes the best about people. We are creating an online community of entrepreneurs and business leaders who struggle with marketing their business online.

This business card should POP! We recently got a new logo and are launching a new website next month, so our business cards should make a statement that feels:
-Fresh
-Smart
-Trustworthy
-Fun

Target Market(s)

small business owners, entrepreneurs

Industry/Entity Type

Digital Marketing

Contact Information for Business Card

Dimensions: 3.5" x 2"

Font styles to use
Sans Serif

Colors
f37122
ffffff

Requirements
Must have
• We need a business card with a modern, bold design. We will use one side of the card as a lead-generation offer, so text on one side will need to fit up to 140 characters. The business card should stick to our core colors (orange, black, and white).
Nice to have
• We think a vertical "portrait" design could be interesting.
Should not have
• Should not look like a traditional business card. The round icon should stand out from a distance.

```html
<!DOCTYPE html>
<html lang="en">
<head>
<meta charset="utf-8">
<title>Larkwell Business Card</title>
<link rel="stylesheet" href="https://fonts.googleapis.com/css2?family=Montserrat:wght@400;600;800&family=Pinyon+Script&family=Covered+By+Your+Grace&display=swap">
<style>
  :root {
    --orange: #f37122;
    --ink: #222222;
    --white: #ffffff;
    --paper: #f4f4f4;
    --silver-light: #f2f2f2;
    --silver-dark: #c9c9c9;
    --stage: #e6e3de;
  }
  * { box-sizing: border-box; margin: 0; padding: 0; }
  html, body { width: 1200px; height: 911px; overflow: hidden; }
  body {
    background: var(--stage);
    font-family: "Montserrat", sans-serif;
    position: relative;
  }
  .card {
    position: absolute;
    overflow: hidden;
    box-shadow: 0 6px 18px rgba(0,0,0,.18);
  }

  /* Front side */
  .card-front {
    left: 60px; top: 284px;
    width: 600px; height: 343px;
    background: var(--paper);
  }
  .front-art { position: absolute; inset: 0; }
  .front-wordmark {
    position: absolute;
    left: 300px; top: 120px;
    width: 240px;
    text-align: center;
    font-weight: 800;
    font-size: 34px;
    letter-spacing: 2px;
    color: var(--white);
  }
  .front-contact {
    position: absolute;
    left: 34px; bottom: 26px;
  }
  .contact-name {
    font-family: "Pinyon Script", cursive;
    font-size: 44px;
    color: var(--ink);
    line-height: 1;
  }
  .contact-role {
    font-weight: 800;
    font-size: 17px;
    letter-spacing: 1px;
    color: var(--orange);
    margin-top: 4px;
  }
  .contact-email {
    font-weight: 400;
    font-size: 16px;
    letter-spacing: .5px;
    color: var(--ink);
    margin-top: 2px;
  }

  /* Back side */
  .card-back {
    left: 760px; top: 155px;
    width: 343px; height: 600px;
    background: var(--orange);
    padding: 22px;
    color: var(--white);
  }
  .note-panel {
    height: 315px;
    border-radius: 14px;
    background: linear-gradient(135deg, var(--silver-light), var(--silver-dark) 55%, var(--silver-light));
    padding: 22px 20px 0;
    text-align: center;
  }
  .brand-dot {
    width: 34px; height: 34px;
    border-radius: 50%;
    background: var(--orange);
    margin: 0 auto 8px;
  }
  .brand-name {
    font-weight: 800;
    font-size: 40px;
    letter-spacing: 1px;
    color: var(--ink);
    line-height: 1;
  }
  .brand-tagline {
    font-family: "Covered By Your Grace", cursive;
    font-size: 17px;
    letter-spacing: 1px;
    color: var(--ink);
    margin-top: 6px;
  }
  .note-lines { margin-top: 12px; }
  .note-line {
    height: 24px;
    border-bottom: 1.5px dotted #7a7a7a;
  }
  .offer-headline {
    margin-top: 22px;
    font-weight: 800;
    font-size: 19px;
    line-height: 1.15;
    text-align: center;
    letter-spacing: .5px;
  }
  .offer-body {
    margin-top: 12px;
    font-weight: 400;
    font-size: 14.5px;
    line-height: 1.3;
    text-align: center;
    letter-spacing: .5px;
  }
  .offer-body strong { font-weight: 600; }
  .offer-link {
    display: block;
    margin: 14px auto 0;
    width: 250px;
    padding: 7px 0;
    border-radius: 20px;
    background: var(--ink);
    color: var(--orange);
    font-weight: 800;
    font-size: 16px;
    text-align: center;
  }
</style>
</head>
<body>

<section class="card card-front" aria-label="Business card front">
  <svg class="front-art" width="600" height="343" viewBox="0 0 600 343" aria-hidden="true">
    <polygon points="250,0 600,0 600,230" fill="var(--ink)"/>
    <circle cx="420" cy="135" r="175" fill="var(--orange)"/>
  </svg>
  <div class="front-wordmark">LARKWELL</div>
  <div class="front-contact">
    <p class="contact-name">Dana Whitfield</p>
    <p class="contact-role">STORY MARKETING COACH</p>
    <p class="contact-email">DANA@LARKWELLNOW.COM</p>
  </div>
</section>

<section class="card card-back" aria-label="Business card back">
  <div class="note-panel">
    <div class="brand-dot"></div>
    <p class="brand-name">LARKWELL</p>
    <p class="brand-tagline">TELL STORIES THAT INSPIRE ACTION</p>
    <div class="note-lines">
      <div class="note-line"></div>
      <div class="note-line"></div>
      <div class="note-line"></div>
      <div class="note-line"></div>
      <div class="note-line"></div>
      <div class="note-line"></div>
    </div>
  </div>
  <p class="offer-headline">REACH MORE PEOPLE.<br>MAKE MORE MONEY.<br>CREATE MORE IMPACT.</p>
  <p class="offer-body">GET YOUR FREE <strong>LARKWELL</strong><br>STARTER PACKAGE AND OUR<br>MARKETING GUIDE TODAY AT</p>
  <span class="offer-link">larkwellnow.com/start</span>
</section>

</body>
</html>
```